Website for software company "velora"

We need a website for our software company/startup named "velora". We are developing several products (currently 3 standard-software products) which are all in different sectors, but all our products are available for Laptops/PC/Mobile Phones/Tablets, ... We do also create custom software and support our customers with consulting to optimize their processes.
We already have a Logo which you can find in the attached files.
We are a young team of 4 members (two founders and 2 employees).

To get an idea of our products -> the first one is a planning software for healthcare organizations (eg. BlueHaven, firebrigade, pharmacy), the second one is a booking software for sport clubs and the third one is a competition software for sports hunting. You see very diverse. Include or ignore this info of our products as you like.

The design has to be a bootstrap 4 (or higher) design. We have licenced FontAwesome as iconset. Responsive design should come without saying.

• Starting page, product pages, news section, contact, team, services

```html
<!DOCTYPE html>
<html lang="en">
<head>
<meta charset="utf-8">
<title>velora – Our Product</title>
<link href="https://fonts.googleapis.com/css2?family=Poppins:wght@400;500;600;700&display=swap" rel="stylesheet">
<style>
:root{
  --ink:#232a35;
  --dark:#222833;
  --orange:#f5812e;
  --text:#555b66;
  --muted:#8b9099;
  --soft:#f3f3f4;
  --line:#e6e7ea;
  --white:#ffffff;
}
*{box-sizing:border-box;margin:0;padding:0}
html,body{width:1200px;height:3257px;overflow:hidden}
body{position:relative;font-family:'Poppins',sans-serif;color:var(--ink);background:var(--white)}
.abs{position:absolute}
a{color:inherit;text-decoration:none}

/* header */
.hero-bg{position:absolute;left:0;top:0}
.brand{position:absolute;left:88px;top:26px;font-size:42px;font-weight:500;color:var(--white);letter-spacing:1px;display:flex;align-items:center;gap:10px}
.brand .dot{width:14px;height:14px;background:var(--orange)}
.nav{position:absolute;left:434px;top:38px;display:flex;gap:30px;font-size:13.5px;font-weight:600;color:var(--white);text-transform:uppercase}
.nav .active{color:var(--orange)}
.login{position:absolute;left:1011px;top:30px;width:100px;height:40px;border:2px solid var(--white);border-radius:3px;color:var(--white);font-size:13.5px;font-weight:600;display:flex;align-items:center;justify-content:center}
.page-title{position:absolute;left:0;width:1200px;top:154px;text-align:center;font-size:46px;font-weight:700;color:var(--white)}
.page-title span{color:var(--orange)}
.crumb{position:absolute;left:0;width:1200px;top:210px;text-align:center;font-size:14px;color:var(--white)}
.mouse{position:absolute;left:590px;top:283px}

/* partners */
.partners-title{position:absolute;left:0;width:1200px;top:454px;text-align:center;font-size:33px;font-weight:600;line-height:38px}
.partners-title .count{color:var(--orange)}
.partner-row{position:absolute;left:190px;top:576px;width:820px;display:flex;justify-content:space-between;font-size:19px;font-weight:500;color:#b7bac0}
.partner{display:flex;align-items:center;gap:8px}
.partner i{width:16px;height:16px;border-radius:50%;border:2px solid #c4c7cc;display:inline-block}

/* about */
.illus{position:absolute;left:95px;top:706px;width:500px;height:354px;border-radius:20px;background:linear-gradient(135deg,#f4f5f7,#fde9d9)}
.eyebrow{position:absolute;left:654px;top:730px;font-size:18px;font-weight:500;color:var(--orange)}
.h2{font-size:33px;font-weight:600;line-height:40px;color:var(--ink)}
.about-h{position:absolute;left:653px;top:753px}
.para{font-size:15.5px;line-height:25.8px;color:var(--text);white-space:nowrap}
.about-p{position:absolute;left:654px;top:839px}
.btn{position:absolute;display:flex;align-items:center;justify-content:center;gap:12px;background:var(--orange);color:var(--white);font-size:14.5px;font-weight:600;border-radius:3px;box-shadow:0 8px 18px rgba(245,129,46,.35);text-transform:uppercase}
.about-btn{left:654px;top:981px;width:156px;height:41px}

/* services */
.services{position:absolute;left:88px;top:1119px;width:1027px;height:538px;background:var(--soft)}
.services-title{position:absolute;left:0;width:1027px;top:86px;text-align:center;font-size:33px;font-weight:600}
.svc{position:absolute;width:300px}
.svc h3{font-size:18.5px;font-weight:600;line-height:24px}
.svc p{font-size:13px;line-height:18.5px;color:var(--text);margin-top:4px}
.svc.left{text-align:right}
.svc-icon{position:absolute}

/* planning */
.plan-h{position:absolute;left:88px;top:1825px}
.plan-p{position:absolute;left:88px;top:1918px}
.plan-btn{left:88px;top:2060px;width:156px;height:41px}
.pager{position:absolute;left:88px;top:2134px;display:flex;gap:7px}
.pager i{width:9px;height:9px;border-radius:50%;background:#b6b9bf;display:block}
.pager i:first-child{background:var(--orange)}
.dashboard{position:absolute;left:636px;top:1764px;width:559px;height:364px;background:linear-gradient(180deg,#f1f2f5,#fafbfc);border-top:12px solid var(--dark);border-left:30px solid #353b46;box-shadow:0 14px 30px rgba(0,0,0,.1)}

/* features */
.features-title{position:absolute;left:0;width:1200px;top:2258px;text-align:center;font-size:33px;font-weight:600}
.feature{position:absolute;width:180px;height:142px;background:var(--white);box-shadow:0 6px 18px rgba(0,0,0,.06);display:flex;flex-direction:column;align-items:center;justify-content:center;gap:12px;font-size:13px;font-weight:500;line-height:17px;text-align:center;color:var(--ink)}
.feature.active{background:var(--orange);color:var(--white)}
.feat-btn{left:494px;top:2645px;width:208px;height:42px}

/* footer */
.footer-bg{position:absolute;left:0;top:2690px}
.foot-brand{position:absolute;left:168px;top:3001px;font-size:52px;font-weight:500;color:var(--white);display:flex;align-items:center;gap:12px}
.foot-brand .dot{width:16px;height:16px;background:var(--orange)}
.social{position:absolute;left:189px;top:3070px;display:flex;gap:9px}
.social i{width:40px;height:40px;border-radius:50%;background:#363d49;display:block}
.fcol{position:absolute;top:2931px;color:var(--white)}
.fcol h4{font-size:19.5px;font-weight:600;margin-bottom:10px}
.fcol li{list-style:none;font-size:13.5px;line-height:31px;color:#c9ccd2}
.fcol li::before{content:"›";margin-right:8px;color:#8a8f98}
.contact li::before{content:none}
.contact li{display:flex;gap:10px;line-height:18px;margin-bottom:17px}
.contact svg{flex:none;margin-top:2px}
.foot-rule{position:absolute;left:88px;top:3208px;width:1024px;height:1px;background:#3a414c}
.copy{position:absolute;left:0;width:1200px;top:3224px;text-align:center;font-size:13.5px;font-weight:600;color:var(--white)}
.to-top{position:absolute;left:1132px;top:3176px;width:42px;height:42px;border-radius:50%;background:var(--orange);display:flex;align-items:center;justify-content:center}
</style>
</head>
<body>

<!-- hero -->
<svg class="hero-bg" width="1200" height="540" viewBox="0 0 1200 540">
  <rect width="1200" height="339" fill="#222833"/>
  <polygon points="0,126 262,339 0,339" fill="#ffffff"/>
  <polygon points="0,146 234,339 0,525" fill="#f5812e"/>
</svg>
<div class="brand"><span class="dot"></span>velora</div>
<nav class="nav">
  <a>&#8962;</a><a>About us</a><a>Services</a><a class="active">Product</a><a>News</a><a>Team</a><a>Contact</a>
</nav>
<a class="login">LOGIN</a>
<h1 class="page-title">Our <span>Product</span></h1>
<div class="crumb">Home / Our Product</div>
<svg class="mouse" width="20" height="32" viewBox="0 0 20 32"><rect x="1.5" y="1.5" width="17" height="29" rx="8.5" fill="none" stroke="#fff" stroke-width="2"/><line x1="10" y1="8" x2="10" y2="13" stroke="#fff" stroke-width="2"/></svg>

<!-- partners -->
<h2 class="partners-title">We’ve <span class="count">1253+</span> More Then Trusted<br>Premium Global Partners</h2>
<svg class="abs" style="left:434px;top:444px" width="118" height="56" viewBox="0 0 118 56"><ellipse cx="59" cy="28" rx="56" ry="25" fill="none" stroke="#232a35" stroke-width="1.5"/></svg>
<div class="partner-row">
  <span class="partner"><i></i>Nortiva</span>
  <span class="partner"><i></i>Lumora</span>
  <span class="partner"><i></i>Quadrel</span>
  <span class="partner"><i></i>Lumora</span>
  <span class="partner"><i></i>Twinly</span>
  <span class="partner"><i></i>Cubrik</span>
</div>

<!-- about -->
<div class="illus" role="img" aria-label="Illustration of a person presenting a network diagram, charts and a calendar on a board"></div>
<div class="eyebrow">ABOUT US</div>
<h2 class="h2 about-h">User Friendly Experience<br>For Your Attendies</h2>
<p class="para about-p">Sed ut perspiciatis unde omnis iste natus error voluptatem<br>accusantium doloremque laudantium, totam rem aperiam,<br>eaque ipsa quae ainventore veritatis et quasi architecto<br>beatae vitae dicta sunt explicabo. Nemo enim ipsam volup-<br>tatem quia voluptas sit aspernatur aut odit .</p>
<a class="btn about-btn">Read more <span>→</span></a>

<!-- services -->
<section class="services">
  <h2 class="services-title">Services We Provide</h2>
  <svg class="abs" style="left:415px;top:156px" width="200" height="310" viewBox="0 0 200 310">
    <defs><filter id="sh" x="-30%" y="-30%" width="160%" height="160%"><feDropShadow dx="8" dy="12" stdDeviation="12" flood-opacity=".12"/></filter></defs>
    <polygon points="0,0 192,155 0,306" fill="#fff" filter="url(#sh)"/>
  </svg>

  <div class="svc left" style="left:9px;top:188px"><h3>SEO Optimization</h3><p>Lorem Ipsum has been the industry's<br>standard dummy text ever.</p></div>
  <div class="svc left" style="left:10px;top:277px"><h3>Web Development</h3><p>Lorem Ipsum has been the industry's<br>standard dummy text ever.</p></div>
  <div class="svc left" style="left:9px;top:361px"><h3>Business Analysis</h3><p>Lorem Ipsum has been the industry's<br>standard dummy text ever.</p></div>

  <div class="svc" style="left:694px;top:188px"><h3>Keyword Research</h3><p>Lorem Ipsum has been the industry's<br>standard dummy text ever.</p></div>
  <div class="svc" style="left:692px;top:277px"><h3>Social Marketing</h3><p>Lorem Ipsum has been the industry's<br>standard dummy text ever.</p></div>
  <div class="svc" style="left:692px;top:361px"><h3>Reporting &amp; Analysis</h3><p>Lorem Ipsum has been the industry's<br>standard dummy text ever.</p></div>

  <svg class="svc-icon" style="left:333px;top:190px" width="52" height="54" viewBox="0 0 52 54" fill="none" stroke="#232a35" stroke-width="1.6"><rect x="2" y="2" width="38" height="46"/><circle cx="17" cy="20" r="8" stroke="#f5812e"/><circle cx="40" cy="42" r="7"/></svg>
  <svg class="svc-icon" style="left:331px;top:286px" width="54" height="52" viewBox="0 0 54 52" fill="none" stroke="#232a35" stroke-width="1.6"><rect x="2" y="2" width="50" height="36"/><line x1="27" y1="38" x2="27" y2="48"/><line x1="16" y1="48" x2="38" y2="48"/><rect x="12" y="12" width="30" height="16" stroke="#f5812e"/></svg>
  <svg class="svc-icon" style="left:329px;top:364px" width="56" height="56" viewBox="0 0 56 56" fill="none" stroke="#232a35" stroke-width="1.6"><path d="M4 52V34M12 52V28M20 52V32M28 52V24"/><polyline points="4,26 14,18 22,22 32,10" stroke="#f5812e"/><circle cx="40" cy="12" r="9"/><line x1="46" y1="19" x2="53" y2="27"/></svg>

  <svg class="svc-icon" style="left:626px;top:190px" width="56" height="56" viewBox="0 0 56 56" fill="none" stroke="#232a35" stroke-width="1.6"><rect x="2" y="2" width="36" height="46"/><line x1="8" y1="30" x2="30" y2="30"/><line x1="8" y1="37" x2="24" y2="37"/><circle cx="19" cy="14" r="5" stroke="#f5812e"/><circle cx="42" cy="42" r="9"/><line x1="48" y1="48" x2="54" y2="54"/></svg>
  <svg class="svc-icon" style="left:625px;top:280px" width="56" height="54" viewBox="0 0 56 54" fill="none" stroke="#232a35" stroke-width="1.6"><rect x="6" y="12" width="44" height="36"/><rect x="2" y="2" width="16" height="12" stroke="#f5812e"/><rect x="38" y="2" width="16" height="12" stroke="#f5812e"/><rect x="16" y="24" width="24" height="16"/></svg>
  <svg class="svc-icon" style="left:625px;top:364px" width="58" height="56" viewBox="0 0 58 56" fill="none" stroke="#232a35" stroke-width="1.6"><rect x="2" y="6" width="38" height="46"/><rect x="12" y="2" width="18" height="8"/><circle cx="20" cy="26" r="7" stroke="#f5812e"/><circle cx="44" cy="42" r="10"/><circle cx="44" cy="42" r="4"/></svg>
</section>

<!-- planning -->
<h2 class="h2 plan-h" style="font-size:34px;line-height:40px">Planning software for<br>healthcare organizations</h2>
<p class="para plan-p">Sed ut perspiciatis unde omnis iste natus error voluptatem<br>accusantium doloremque laudantium, totam rem aperiam,<br>eaque ipsa quae ainventore veritatis et quasi architecto<br>beatae vitae dicta sunt explicabo. Nemo enim ipsam volup-<br>tatem quia voluptas sit aspernatur aut odit .</p>
<a class="btn plan-btn">Read more <span>→</span></a>
<div class="pager"><i></i><i></i><i></i></div>
<div class="dashboard" role="img" aria-label="Screenshot of the planning software dashboard with regional sales charts and statistics"></div>

<!-- features -->
<h2 class="features-title">Most Prominent Features</h2>

<div class="feature" style="left:223px;top:2319px">
  <svg width="46" height="46" viewBox="0 0 46 46" fill="none" stroke="#232a35" stroke-width="1.6"><rect x="2" y="4" width="34" height="28"/><line x1="2" y1="11" x2="36" y2="11"/><rect x="8" y="16" width="14" height="10" stroke="#f5812e"/><path d="M30 26l12 6-5 2 4 6-3 2-4-6-4 4z"/></svg>
  <span>Drag &amp; Drop<br>Form Builder</span></div>
<div class="feature" style="left:412px;top:2319px">
  <svg width="46" height="46" viewBox="0 0 46 46" fill="none" stroke="#232a35" stroke-width="1.6"><rect x="3" y="7" width="40" height="36" rx="3"/><line x1="13" y1="3" x2="13" y2="11"/><line x1="33" y1="3" x2="33" y2="11"/><line x1="23" y1="17" x2="23" y2="29" stroke="#f5812e"/><circle cx="23" cy="35" r="1.5" fill="#f5812e" stroke="none"/></svg>
  <span>Limit and<br>Schedule</span></div>
<div class="feature active" style="left:602px;top:2319px">
  <svg width="50" height="50" viewBox="0 0 50 50" fill="none" stroke="#fff" stroke-width="1.8"><circle cx="25" cy="25" r="18"/><circle cx="25" cy="25" r="8"/><path d="M25 2v10M25 38v10M2 25h10M38 25h10"/></svg>
  <span>CAPTCHA<br>Support</span></div>
<div class="feature" style="left:792px;top:2319px">
  <svg width="42" height="50" viewBox="0 0 42 50" fill="none" stroke="#232a35" stroke-width="1.6"><path d="M2 2h26l12 12v34H2z"/><path d="M28 2v12h12"/><path d="M21 36V20M14 27l7-7 7 7" stroke="#f5812e"/></svg>
  <span>File Upload</span></div>

<div class="feature" style="left:223px;top:2473px">
  <svg width="48" height="48" viewBox="0 0 48 48" fill="none" stroke="#232a35" stroke-width="1.6"><rect x="10" y="2" width="28" height="36"/><line x1="16" y1="12" x2="32" y2="12"/><line x1="16" y1="19" x2="32" y2="19" stroke="#f5812e"/><line x1="16" y1="26" x2="32" y2="26"/><path d="M2 38h44v6H2z"/></svg>
  <span>Data Entry<br>Management</span></div>
<div class="feature" style="left:412px;top:2473px">
  <svg width="36" height="48" viewBox="0 0 36 48" fill="none" stroke="#232a35" stroke-width="1.6"><rect x="4" y="2" width="28" height="44" rx="5"/><rect x="9" y="12" width="18" height="14" stroke="#f5812e"/><line x1="10" y1="34" x2="26" y2="34"/></svg>
  <span>Custom Form<br>Field Validations</span></div>
<div class="feature" style="left:602px;top:2473px">
  <svg width="48" height="48" viewBox="0 0 48 48" fill="none" stroke="#232a35" stroke-width="1.6"><path d="M44 4C30 4 18 14 14 28l6 6c14-4 24-16 24-30z"/><circle cx="31" cy="17" r="4" stroke="#f5812e"/><path d="M14 28l-8 2 6-10M20 34l-2 8 10-6"/><path d="M10 38l-6 6" stroke="#f5812e"/></svg>
  <span>Fully Optimized<br>for Page Speed</span></div>
<div class="feature" style="left:792px;top:2473px">
  <svg width="48" height="48" viewBox="0 0 48 48" fill="none" stroke="#232a35" stroke-width="1.6"><rect x="4" y="4" width="12" height="10"/><rect x="32" y="4" width="12" height="10"/><rect x="4" y="34" width="12" height="10"/><rect x="32" y="34" width="12" height="10"/><rect x="18" y="18" width="12" height="12" stroke="#f5812e"/><path d="M10 14v20M38 14v20M16 24h2M30 24h2"/></svg>
  <span>Server-Side<br>Validation</span></div>

<a class="btn feat-btn">See all features <span>→</span></a>

<!-- footer -->
<svg class="footer-bg" width="1200" height="567" viewBox="0 0 1200 567">
  <polygon points="0,174 1200,10 1200,567 0,567" fill="#e9eaec"/>
  <polygon points="0,250 1200,44 1200,567 0,567" fill="#222833"/>
</svg>
<div class="foot-brand"><span class="dot"></span>velora</div>
<div class="social" aria-label="Social links"><i></i><i></i><i></i><i></i></div>

<div class="fcol" style="left:465px"><h4>Quick Links</h4>
  <ul><li>Home</li><li>Our Product</li><li>Our Services</li><li>Our Team</li><li>Latest news</li><li>Contact Us</li></ul></div>
<div class="fcol" style="left:663px"><h4>Information</h4>
  <ul><li>Privacy Policy</li><li>Terms &amp; Conditions</li><li>Shipping Policy</li><li>FAQ's</li><li>Sitemap</li><li>Blog</li></ul></div>
<div class="fcol contact" style="left:873px"><h4>Contact info</h4>
  <ul>
    <li><svg width="13" height="11" viewBox="0 0 13 11"><rect width="13" height="11" rx="1" fill="#f5812e"/><path d="M1 1l5.5 5L12 1" fill="none" stroke="#222833"/></svg><span>Email:<br>info@velora.com.au</span></li>
    <li><svg width="13" height="13" viewBox="0 0 13 13"><path d="M3 0l2 3-1.5 1.5a8 8 0 0 0 5 5L10 8l3 2-1.5 3C6 13 0 7 0 1.5z" fill="#f5812e"/></svg><span>Phone:<br>08 555-010-2040</span></li>
    <li><svg width="12" height="15" viewBox="0 0 12 15"><path d="M6 0a6 6 0 0 1 6 6c0 4-6 9-6 9S0 10 0 6a6 6 0 0 1 6-6z" fill="#f5812e"/><circle cx="6" cy="6" r="2.2" fill="#222833"/></svg><span>Location:<br>Some address line goes<br>here city name country</span></li>
  </ul></div>

<div class="foot-rule"></div>
<div class="copy">© Copyright 2022 velora, All Rights Reserved</div>
<a class="to-top" aria-label="Back to top"><svg width="14" height="16" viewBox="0 0 14 16" fill="none" stroke="#fff" stroke-width="1.6"><path d="M7 15V2M1 8l6-6 6 6"/></svg></a>

</body>
</html>
```